New word press website site design

We provide email marketing to aircraft brokers and dealers to assist in finding buyers for their aircraft.

Our target market to purchase our broadcasts are the aircraft sellers – NOT the buyers.

Our target market when sending the email broadcast, are the buyers (end users).

The website should target brokers and our email database targets the buyers.

We do not buy or sell aircraft as a company. We provide email marketing solutions to connect buyers and sellers of aircraft.

Our other site is planelantern.com and will be redesigned soon. Please use it as a reference as far as general scope but they layout can be completely different and should include helicopters only as far as imagery. The colors should be similar as the logos are similar, however we do NOT want both sites to be identical in use of primary color

Plenty of images and sample broadcasts attached to use as needed throughout the site.

Headlines listed below with some text copy.

In the event that we need to add more text, please use standard greek text as a place holder for the purposes of the mockup design.

Need to have a “SUBSCRIBE” button to join our mailing list.

Possible Headlines:

Exclusively Showcasing Rotor Wing Aircraft to the Global Marketplace

Showcasing Pre-Owned Helicopters Available For Sale, Lease, Trade, or Wanted for Acquisition.

Mobile-optimized Email Campaigns that Render Correctly Across all Devices

Targeted worldwide recipients that currently own, operate, or have an interest in rotor wing aircraft

STRONGEST Rotor Wing Database in the Industry

Text/Copy:

HOME
Rotorbay Vista is one of most powerful marketing tools in the industry to utilize in reaching targeted buyers of pre-owned helicopters. Rotorbay Vista provides the rotor wing aircraft market with a fast, effective, and affordable email broadcast solution to utilize in the marketing of Helicopters for sale.

Developed Exclusively to Showcase Rotor Wing Aircraft to the Global marketplace, Rotorbay Vista is a powerful tool designed to maximize leads and accelerate the sales process by providing the ability to reach a global network of Helicopter buyers in a matter of seconds.

DATABASE:

While Rotorbay Vista is delivered to all known broker/dealers, our primary focus is in reaching end users. Our opt-in/opt-out recipient database is updated daily and developed specifically to deliver the latest details on helicopters available for sale or lease to the inboxes of a global network of Helicopter buyers and sellers.

· Helicopter Owners

· Helicopter Operators

· Helicopter Charter Services

· Helicopter Management Companies

· Corporate/Municipal Flight Departments

· Helicopter Pilots

· Senior Aviation Executives

· Wealth Management Firms

· High Net Worth Individuals

· Helicopter Broker/Dealers

Helicopter Tour/Travel Firms

· Off Shore Oil & Gas Production Firms

· Municipalities/Media/Medevac Firms

Our recipient database is continuously updated and developed specifically to reach buyers and sellers of Helicopters. This ensures that your Helicopter will be showcased to the right people. Rotorbay Vista does not broadcast non-rotor wing aircraft and focuses exclusively on the Global Helicopter Market.

Broadcast Design:

Rotorbay Vista broadcast ads are custom designed for you by incorporating your corporate image and branding. Because you have worked hard in developing your corporate image, we strive to maintain it while designing an ad that will showcase your Helicopter to its best advantage. Rotorbay Vista utilizes Mobile-optimized Email Campaigns with Responsive Coding to render correctly across all devices

Once you have approved the design, we schedule the broadcast to be sent on the available date and time you request. The broadcast will link to your website and the results can be immediate. All email leads and replies will go to the email address that you provided.

Pricing:
Create a place holder for 3 Different Broadcast Packages

-Broadcast Package A
-Broadcast Package B
-Broadcast Package C

Target Market(s)

The target market is any person or company that has aircraft for sale. We work with brokers, dealers, and owners to assist in finding buyers for their aircraft using email marketing campaigns (Showcase broadcasts).

Industry/Entity Type

Aviation

Colors
0255a3
00a990

Requirements
Nice to have
• Samples of helicopter for sale broadcast ads in /image gallery/slider

```html
<!DOCTYPE html>
<html lang="en">
<head>
<meta charset="UTF-8">
<title>Rotorline Media Inc — Rotorbay Vista</title>
<link rel="stylesheet" href="https://fonts.googleapis.com/css2?family=Bebas+Neue&family=Mulish:wght@400;500;600&display=swap">
<style>
  :root {
    --navy: #2d2c82;
    --red: #d8263b;
    --ink: #1e1e24;
    --white: #ffffff;
    --night: #1b1d22;
    --rule: #c9c9cf;
  }
  * { box-sizing: border-box; margin: 0; padding: 0; }
  html, body { width: 1200px; height: 3509px; overflow: hidden; background: var(--white); }
  body { position: relative; font-family: "Mulish", "Helvetica Neue", Arial, sans-serif; color: var(--ink); }
  .display { font-family: "Bebas Neue", "Oswald", Impact, sans-serif; font-weight: 400; letter-spacing: 0.5px; }

  /* Header */
  .site-header { position: absolute; left: 0; top: 0; width: 1200px; height: 205px; }
  .brand { position: absolute; left: 30px; top: 96px; display: flex; align-items: center; gap: 16px; }
  .brand-dot { width: 22px; height: 22px; border-radius: 50%; background: var(--red); }
  .brand-name { font-size: 58px; line-height: 1; color: var(--navy); }
  .btn-subscribe { position: absolute; left: 947px; top: 54px; width: 223px; height: 84px; background: var(--navy); color: var(--white); font-size: 42px; display: flex; align-items: center; justify-content: center; text-decoration: none; }
  .header-rule { position: absolute; left: 30px; top: 199px; width: 1140px; height: 4px; background: var(--red); }

  /* Hero */
  .hero { position: absolute; left: 0; top: 210px; width: 1200px; height: 690px; background: linear-gradient(180deg, #3f5873 0%, #6f8496 38%, #49524f 62%, #30352f 100%); }
  .hero-title { position: absolute; left: 0; top: 92px; width: 1200px; text-align: center; color: var(--white); font-size: 50px; line-height: 64px; }

  .feature-frame { position: absolute; left: 30px; top: 741px; width: 1140px; height: 398px; background: var(--white); border: 4px solid var(--red); border-radius: 4px; }
  .feature-card { position: absolute; top: 15px; width: 538px; height: 358px; border-radius: 6px; color: var(--white); padding: 40px 28px; }
  .feature-card.sale { left: 20px; background: linear-gradient(180deg, #2b3a55 0%, #6a6f7e 45%, #d68a3f 80%, #f3b55a 100%); }
  .feature-card.mobile { left: 578px; background: linear-gradient(180deg, #4d5260 0%, #8a8270 55%, #b7a77f 100%); }
  .feature-card h2 { font-size: 46px; line-height: 1; }
  .feature-card p { font-family: "Bebas Neue", "Oswald", Impact, sans-serif; font-size: 36px; line-height: 1.2; margin-top: 6px; }
  .frame-shadow { position: absolute; left: 150px; top: 1139px; width: 900px; height: 40px; background: radial-gradient(ellipse at 50% 0%, rgba(0,0,0,0.16) 0%, rgba(0,0,0,0) 70%); }

  /* Broadcast design */
  .broadcast { position: absolute; left: 40px; top: 1265px; width: 1122px; text-align: center; }
  .section-title { font-size: 58px; line-height: 1; color: var(--red); }
  .broadcast p { font-size: 25.5px; line-height: 39px; margin-top: 40px; }
  .broadcast p + p { margin-top: 36px; }

  /* Showcase gallery */
  .showcase { position: absolute; left: 0; top: 1827px; width: 1200px; height: 751px; background: linear-gradient(180deg, #15171b 0%, #2a2c30 55%, #1a1b1e 100%); }
  .showcase-title { position: absolute; left: 0; top: 92px; width: 1200px; text-align: center; color: var(--white); font-size: 54px; }
  .showcase-rule { position: absolute; left: 522px; top: 190px; width: 156px; height: 3px; background: var(--white); }
  .slide { position: absolute; top: 294px; width: 368px; height: 260px; background: var(--white); border-radius: 3px; display: flex; align-items: center; justify-content: center; }
  .slide .art { width: 290px; height: 170px; border-radius: 4px; }
  .slide.s1 { left: 33px; } .slide.s1 .art { background: radial-gradient(ellipse at center, #d8262a 0%, #e8a3a3 55%, #ffffff 75%); }
  .slide.s2 { left: 416px; } .slide.s2 .art { background: radial-gradient(ellipse at center, #f29a1e 0%, #f6d39c 55%, #ffffff 75%); }
  .slide.s3 { left: 798px; } .slide.s3 .art { background: radial-gradient(ellipse at center, #2f78bd 0%, #b9d3ea 55%, #ffffff 75%); }
  .dots { position: absolute; left: 0; top: 637px; width: 1200px; display: flex; justify-content: center; gap: 10px; }
  .dots span { width: 26px; height: 26px; border-radius: 50%; background: #6b6d72; }
  .dots span.active { background: var(--white); }

  /* About */
  .about { position: absolute; left: 30px; top: 2695px; width: 684px; }
  .about .brand-name { display: block; font-size: 58px; }
  .about p { font-size: 24.5px; line-height: 38px; text-align: justify; margin-top: 64px; }
  .about p + p { margin-top: 36px; }
  .promo { position: absolute; left: 753px; top: 2669px; width: 417px; height: 620px; border-radius: 4px; overflow: hidden; background: linear-gradient(150deg, #1c2334 0%, #2d4f70 38%, #8aa0b6 52%, #d23d52 68%, #d8263b 100%); color: var(--white); }
  .promo .top { position: absolute; left: 30px; top: 32px; font-size: 52px; line-height: 64px; }
  .promo .bottom { position: absolute; right: 18px; bottom: 30px; font-size: 40px; line-height: 54px; text-align: right; }

  /* Footer */
  .footer-rule { position: absolute; left: 30px; top: 3391px; width: 1140px; height: 2px; background: var(--rule); }
  .footer-note { position: absolute; left: 0; top: 3430px; width: 1200px; text-align: center; font-size: 28px; font-weight: 500; }
</style>
</head>
<body>
  <header class="site-header">
    <div class="brand"><span class="brand-name display">Rotorline Media Inc</span></div>
    <a class="btn-subscribe display" href="#subscribe">Subscribe</a>
    <div class="header-rule"></div>
  </header>

  <section class="hero" role="img" aria-label="Photo of a black and gold helicopter parked on a helipad under a cloudy sky">
    <h1 class="hero-title display">Exclusively showcasing rotor wing aircraft to the<br>global marketplace</h1>
  </section>

  <div class="feature-frame">
    <article class="feature-card sale" role="img" aria-label="Photo of a helicopter flying at sunset">
      <h2 class="display">Pre-Owned Helicopters</h2>
      <p>Available for sale</p>
    </article>
    <article class="feature-card mobile" role="img" aria-label="Photo of a helicopter in flight against a hazy sky">
      <h2 class="display">Mobile-Optimized</h2>
      <p>Email campaigns</p>
    </article>
  </div>
  <div class="frame-shadow"></div>

  <section class="broadcast">
    <h2 class="section-title display">Broadcast Design</h2>
    <p>Rotorbay Vista broadcast ads are custom designed for you by incorporating your corporate image and branding. Because you have worked hard in developing your corporate image, we strive to maintain it while designing an ad that will showcase your Helicopter to its best advantage. Rotorbay Vista utilizes Mobile-optimized Email Campaigns with Responsive Coding to render correctly across all devices</p>
    <p>Once you have approved the design, we schedule the broadcast to be sent on the available date and time you request. The broadcast will link to your website and the results can be immediate. All email leads and replies will go to the email address that you provided.</p>
  </section>

  <section class="showcase" role="region" aria-label="Rotorbay Vista gallery">
    <h2 class="showcase-title display">Rotorbay Vista</h2>
    <div class="showcase-rule"></div>
    <div class="slide s1"><div class="art" role="img" aria-label="Red rescue helicopter"></div></div>
    <div class="slide s2"><div class="art" role="img" aria-label="Orange and black light helicopter"></div></div>
    <div class="slide s3"><div class="art" role="img" aria-label="White and blue helicopter"></div></div>
    <div class="dots"><span class="active"></span><span></span><span></span><span></span><span></span></div>
  </section>

  <section class="about">
    <span class="brand-name display">Rotorline Media Inc</span>
    <p>Nemo enim ipsam voluptatem quia voluptas sit aspernatur aut odit aut fugit, sed quia consequuntur magni dolores eos qui ratione voluptatem sequi nesciunt. Neque porro quisquam est, qui dolorem ipsum quia dolor sit amet, consectetur, adipisci velit, sed quia non numquam eius.</p>
    <p>Ut enim ad minima veniam, quis nostrum exercitationem ullam corporis suscipit laboriosam, nisi ut aliquid ex ea commodi consequatur.</p>
  </section>

  <aside class="promo" role="img" aria-label="White and red medical helicopter over a diagonal navy and red background">
    <div class="top display">Rotor Wing<br>Aircraft</div>
    <div class="bottom display">Global Network<br>of Helicopter</div>
  </aside>

  <div class="footer-rule"></div>
  <footer class="footer-note">Copyrights @ 2018 Rotorline Media Inc. All Rights Reserved.</footer>
</body>
</html>
```